Label design for organic saffron, saffron and herbal syrup

We cultivate saffron, Damszen roses, flowers and herbs. We would need a recognizable outfit (label) for our products. Theoretically (and practically) we have "converted" the family coat of arms into a kind of LOGO. I would send this in the attachment. It would be nice if - in one way or another - this LOGO / coat of arms could be used (certainly with other colors). For some time we have played with the idea of changing the second part of the family name "Wallmoser" (in German .... greuth sounds similar to Kraut / herb [English]) .... eg Wallmoser's saffron syrup into the labeling.
Our products are primarily syrups, currently herbal syrup and saffron syrup. Here the first problem arises, the only bottles / caps that are actually approved for syrup filling (hot filling) are appallingly ugly (see attachment), the only possibility of "sprucing up" is to use so-called "shrink sleeves" (here we need a diameter of 31 and a length of about 40), the colors of which are also limited. Besides the syrup, we sell saffron as a spice and various herbal mixtures (see appendix current packaging saffron). Our quantities are small (syrup 200ml-330ml), saffron in the gram range.
We also need quasi the back of the labeling (this should be able to be redefined per charge) .... Batch 1 (with small quantity has eg more of herb xy than the next batch or the saffron syrup with batch xy needs more / less saffron). In addition, we are certified organic (for this reason, the reverse side would also have to contain all the requirements of organic labeling) [see attachment].
We do not really want to address a specific clientele. Maybe just people who want to taste, enjoy, mix drinks, cook .... (and - unfortunately - don't like Corvel syrup :-) and want to pay a bit more, or find our saffron or herbs better than others) .
In summary
- Strong recognition value (possibly inclusion of "coat of arms", color variable ... although I personally don't like yellow that much)
- Saffron syrup (the color of the saffron syrup is yellow / golden-yellow-light orange, in a transparent ugly bottle)
- Herbal syrup (color variable from blue / green / brown / red elements, in transparent ugly bottle)
Saffron and other herbs (very small containers, type of container not yet fixed)
Regarding a potential "style" I can unfortunately give little information. On the one hand, I am in love with minimalism, on the other hand, I find the translucent, cryptic, implied enormously attractive and sometimes even the "overloaded" colorful has its charm. I think that all in all, it just has to be coherent, and then it will be good.
Requirements
Must have
- Integration of Code of Arms, modifiable for different products

```html
<!DOCTYPE html>
<html lang="en">
<head>
<meta charset="utf-8">
<title>Eprouvette Label – Wallmoser Organic Saffron</title>
<link rel="stylesheet" href="https://fonts.googleapis.com/css2?family=Arimo:wght@400&family=Open+Sans:wdth,wght@75,700&display=swap">
<style>
  :root {
    --page: #ffffff;
    --stage: #bcbdbf;
    --ink: #111111;
    --navy: #2b2370;
    --tube: #ffffff;
    --tube-edge: #d9d9db;
    --organic-light: #c6e1a6;
    --organic-leaf: #8cc63f;
    --organic-seal: #e8f3de;
    --box-line: #222222;
  }
  * { margin: 0; padding: 0; box-sizing: border-box; }
  html, body {
    width: 784px; height: 1200px; overflow: hidden;
    background: var(--page);
  }
  .sheet { position: relative; width: 784px; height: 1200px; }
  .stage {
    position: absolute; left: 47px; top: 47px; width: 692px; height: 1106px;
    background: var(--stage);
  }
  .sheet-title, .view-label {
    position: absolute; font-family: "Open Sans", sans-serif;
    font-stretch: 75%; font-weight: 700; color: var(--ink);
    transform: translateX(-50%); letter-spacing: 1px; white-space: nowrap;
  }
  .sheet-title { left: 398px; top: 132px; font-size: 48px; }
  .view-label { top: 230px; font-size: 36px; }
  .view-label--front { left: 260px; }
  .view-label--back { left: 524px; }

  .tube {
    position: absolute; top: 315px; height: 668px;
    background: var(--tube);
    border-radius: 4px 4px 52px 52px;
  }
  .tube::before {
    content: ""; position: absolute; left: -5px; right: -5px; top: 0; height: 12px;
    background: var(--tube); border: 1px solid var(--tube-edge); border-radius: 6px;
  }
  .tube--front { left: 210px; width: 100px; }
  .tube--back { left: 468px; width: 106px; }

  .vertical {
    position: absolute; writing-mode: vertical-rl; white-space: nowrap;
    color: var(--navy);
  }
  .brand-mark {
    position: absolute; left: 26px; top: 60px; width: 48px; height: 48px;
    border-radius: 50%; background: var(--navy);
  }
  .brand-name {
    left: 37px; top: 126px; font-family: "Arimo", sans-serif; font-size: 24px;
  }
  .product-name {
    left: 34px; top: 326px; font-family: "Arimo", sans-serif; font-size: 27px;
  }
  .product-weight {
    left: 41px; top: 548px; font-family: "Arimo", sans-serif; font-size: 18px; letter-spacing: 1px;
  }

  .maker-info {
    left: 28px; top: 58px; font-family: "Open Sans", sans-serif; font-stretch: 75%;
    font-weight: 700; font-size: 13px; line-height: 13px;
  }
  .organic-block {
    position: absolute; left: 20px; top: 350px; width: 57px; height: 112px;
    background: var(--organic-light);
  }
  .organic-seal {
    position: absolute; left: 18px; top: 6px; width: 24px; height: 24px;
    border-radius: 50%; background: var(--organic-seal);
  }
  .organic-leaf {
    position: absolute; left: 6px; top: 42px; width: 45px; height: 36px;
    background: var(--organic-leaf);
  }
  .best-before {
    position: absolute; left: 22px; top: 489px; width: 56px; height: 127px;
    background: var(--tube); border: 1.5px solid var(--box-line);
  }
  .best-before-label {
    right: 6px; top: 8px; color: var(--ink); font-family: "Open Sans", sans-serif;
    font-stretch: 75%; font-weight: 700; font-size: 13px;
  }
</style>
</head>
<body>
<main class="sheet">
  <div class="stage"></div>
  <h1 class="sheet-title">Eprouvette</h1>
  <p class="view-label view-label--front">Front</p>
  <p class="view-label view-label--back">Back</p>

  <section class="tube tube--front" aria-label="Front label">
    <div class="brand-mark"></div>
    <p class="vertical brand-name">Wallmoser</p>
    <p class="vertical product-name">Organic SAFRAN</p>
    <p class="vertical product-weight">1.0 gram</p>
  </section>

  <section class="tube tube--back" aria-label="Back label">
    <p class="vertical maker-info">Expertly crafted by: Halden-Wallmoser<br>1234 Street Name, Any City, District, Country</p>
    <div class="organic-block" role="img" aria-label="Organic certification marks">
      <div class="organic-seal"></div>
      <div class="organic-leaf"></div>
    </div>
    <div class="best-before">
      <p class="vertical best-before-label">Best Before:</p>
    </div>
  </section>
</main>
</body>
</html>
```